A Label for an ECO Friendly Spirit Company

Design a label which can be used for vodka and gin (London Dry Gin). It should be Square type Like the Shape File you see in the uploads. KIRO means Kind Inventive Rare and Original. We want a cool and slim label that calls for eco-friendly. We want to use it for our premium
Vodka and our London Dry Gin. Please use the logo and design it in Square Type.

40%vol, 700ml

Target Market(s)

spirits and events

Industry/Entity Type

SPIRITS

Colors
00AB8E
00BBA5
67D7C9
C6EFE9
E9F9F6
59FF00
82FF00
B8FF75
E3FFCB
F4FFEA

Requirements
Must have
• Logo from KIRO, Squaee Shape

```html
<!DOCTYPE html>
<html lang="en">
<head>
<meta charset="utf-8">
<title>KIRO Premium Vodka Label</title>
<link rel="stylesheet" href="https://fonts.googleapis.com/css2?family=Montserrat:wght@400;500;600;700&display=swap">
<style>
  :root {
    --teal-deep: #00ab8e;
    --teal: #00bba5;
    --teal-light: #67d7c9;
    --mint: #c6eff0;
    --lime: #7cc21f;
    --white: #ffffff;
    --backdrop: #e7ecf4;
  }
  html, body {
    margin: 0;
    padding: 0;
    width: 1200px;
    height: 800px;
    overflow: hidden;
    background: var(--backdrop);
  }
  .artboard {
    width: 1200px;
    height: 800px;
    display: block;
    font-family: "Montserrat", sans-serif;
  }
  .brand-name { fill: var(--teal-deep); font-weight: 600; }
  .brand-tagline { fill: var(--teal-deep); font-weight: 600; }
  .brand-tagline--accent { fill: var(--lime); font-weight: 500; }
  .brand-square { fill: var(--teal); }
  .brand-divider { stroke: var(--teal-deep); stroke-width: 2; }

  .label-face { fill: url(#labelGradient); }
  .label-frame { fill: none; stroke: var(--white); }
  .label-mark { fill: var(--white); }
  .ribbon-band { fill: var(--white); }
  .ribbon-tail { fill: var(--mint); }
  .ribbon-edge { fill: none; stroke: var(--teal); stroke-width: 1.5; }
  .ribbon-word { fill: var(--teal-deep); font-weight: 700; }
  .label-premium { fill: var(--white); font-weight: 400; }
  .label-product { fill: var(--white); font-weight: 500; }
  .label-rule { stroke: var(--white); stroke-width: 1.5; }
  .label-pill { fill: var(--white); }
  .label-pill-text { fill: var(--teal-deep); font-weight: 600; }
  .label-pill-text--accent { fill: var(--lime); font-weight: 600; }
  .label-capsule { fill: none; stroke: var(--white); stroke-width: 1.2; }
  .label-spec { fill: var(--white); font-weight: 400; }
</style>
</head>
<body>
<svg class="artboard" viewBox="0 0 1200 800" xmlns="http://www.w3.org/2000/svg">
  <defs>
    <linearGradient id="labelGradient" x1="0" y1="0" x2="1" y2="1">
      <stop offset="0" stop-color="#19c1ab"/>
      <stop offset="0.45" stop-color="#3ccdb9"/>
      <stop offset="1" stop-color="#00ab8e"/>
    </linearGradient>
  </defs>

  <!-- Brand lockup -->
  <g class="brand-lockup">
    <rect class="brand-square" x="432" y="44" width="72" height="72" rx="8"/>
    <line class="brand-divider" x1="522" y1="40" x2="522" y2="124"/>
    <text class="brand-name" x="536" y="96" font-size="80">KIRO</text>
    <text class="brand-tagline" x="538" y="112" font-size="12.5">KIND INVENTIVE</text>
    <text class="brand-tagline brand-tagline--accent" x="538" y="126" font-size="9.5" letter-spacing="3.2">RARE AND ORIGINAL</text>
  </g>

  <!-- Square label, set on point -->
  <g class="product-label">
    <polygon class="label-face" points="600,170 900,470 600,770 300,470"/>
    <polygon class="label-frame" stroke-width="2" points="600,186 884,470 600,754 316,470"/>
    <polygon class="label-frame" stroke-width="1" points="600,196 874,470 600,744 326,470"/>

    <rect class="label-mark" x="568" y="278" width="64" height="64" rx="7"/>

    <g class="label-ribbon">
      <polygon class="ribbon-tail" points="452,386 506,386 506,432 452,432 472,409"/>
      <polygon class="ribbon-tail" points="748,386 694,386 694,432 748,432 728,409"/>
      <rect class="ribbon-band" x="494" y="366" width="212" height="50"/>
      <rect class="ribbon-edge" x="499" y="371" width="202" height="40"/>
      <text class="ribbon-word" x="600" y="406" font-size="40" letter-spacing="9" text-anchor="middle">KIRO</text>
    </g>

    <text class="label-premium" x="600" y="458" font-size="13" letter-spacing="3" text-anchor="middle">PREMIUM</text>

    <g class="label-product-line">
      <line class="label-rule" x1="470" y1="484" x2="504" y2="484"/>
      <line class="label-rule" x1="476" y1="490" x2="504" y2="490"/>
      <line class="label-rule" x1="470" y1="496" x2="504" y2="496"/>
      <line class="label-rule" x1="696" y1="484" x2="730" y2="484"/>
      <line class="label-rule" x1="696" y1="490" x2="724" y2="490"/>
      <line class="label-rule" x1="696" y1="496" x2="730" y2="496"/>
      <text class="label-product" x="602" y="504" font-size="38" letter-spacing="12" text-anchor="middle">VODKA</text>
    </g>

    <rect class="label-pill" x="466" y="530" width="268" height="21" rx="2"/>
    <text class="label-pill-text" x="600" y="546" font-size="15.5" text-anchor="middle">KIND INVENTIVE</text>

    <rect class="label-pill" x="466" y="558" width="268" height="21" rx="2"/>
    <text class="label-pill-text label-pill-text--accent" x="600" y="574" font-size="12.5" letter-spacing="4" text-anchor="middle">RARE AND ORIGINAL</text>

    <rect class="label-capsule" x="503" y="594" width="194" height="28" rx="14"/>
    <text class="label-spec" x="556" y="614" font-size="16" text-anchor="middle">40%vol</text>
    <text class="label-spec" x="648" y="614" font-size="16" text-anchor="middle">700ml</text>
  </g>
</svg>
</body>
</html>
```